Whitcombe Business Card Design

The name of the business is Dario Whitcombe, CPA LLC
The service that we offer is Accounting, Tax & Consulting Services. I need it to have the following items:
Dario Whitcombe, Principal
Phone Number
Email Address
Physical Address

I have attached the company logo, one in black and one in white. Please provide a design in black background and the other in white background. Please include "Accounting, Tax & Consulting Services". I want the business card to be clean and very professional.

```html
<!DOCTYPE html>
<html lang="en">
<head>
<meta charset="utf-8">
<title>Dario Whitcombe, CPA LLC — Business Cards</title>
<link rel="stylesheet" href="https://fonts.googleapis.com/css2?family=Lato:wght@400;700&display=swap">
<style>
  :root {
    --backdrop: #2a2a2c;
    --card-black: #0a0a0a;
    --brand-red: #9d161b;
    --white: #ffffff;
    --grey: #9a9a9a;
  }
  * { box-sizing: border-box; margin: 0; padding: 0; }
  html, body {
    width: 1200px; height: 1015px; overflow: hidden;
    background: var(--backdrop);
    font-family: "Lato", sans-serif;
  }
  .canvas {
    width: 1200px; height: 1015px;
    display: flex; flex-direction: column; align-items: center; justify-content: center;
    gap: 56px;
  }
  .card {
    width: 700px; height: 400px;
    position: relative; overflow: hidden;
    box-shadow: 0 18px 40px rgba(0,0,0,.55);
  }

  /* Front */
  .card-front { background: var(--card-black); }
  .front-brand {
    position: absolute; left: 0; right: 0; top: 0; height: 290px;
    display: flex; flex-direction: column; align-items: center; justify-content: center;
  }
  .brand-row { display: flex; align-items: center; gap: 16px; }
  .brand-mark { width: 26px; height: 26px; background: var(--brand-red); }
  .brand-name {
    color: var(--white); font-weight: 700; font-size: 34px;
    letter-spacing: 1px; text-transform: uppercase;
  }
  .brand-tagline {
    margin-top: 10px; color: var(--grey); font-size: 19px;
    letter-spacing: 4.5px; text-transform: uppercase;
  }
  .service-band {
    position: absolute; left: 0; right: 0; bottom: 0; height: 110px;
    background: var(--brand-red);
    display: flex; align-items: center; justify-content: center;
  }
  .service-line {
    color: var(--white); font-size: 21px; letter-spacing: 1.2px; text-transform: uppercase;
  }

  /* Back */
  .card-back { background: var(--brand-red); color: var(--white); }
  .contact-block { position: absolute; left: 70px; top: 70px; }
  .person-name { font-size: 32px; letter-spacing: 1px; text-transform: uppercase; line-height: 1; }
  .person-role { font-size: 20px; margin-top: 4px; }
  .contact-list { list-style: none; margin-top: 52px; padding-left: 40px; }
  .contact-list li { display: flex; align-items: center; gap: 10px; font-size: 20px; line-height: 1.35; }
  .contact-list svg { width: 18px; height: 18px; fill: var(--white); }
  .address { margin-top: 46px; padding-left: 86px; font-size: 20px; line-height: 1.3; }
</style>
</head>
<body>
<main class="canvas">
  <section class="card card-front" aria-label="Card front">
    <div class="front-brand">
      <div class="brand-row">
        <span class="brand-mark"></span>
        <span class="brand-name">Dario Whitcombe, CPA, LLC</span>
      </div>
      <p class="brand-tagline">Certified Public Accountant</p>
    </div>
    <div class="service-band">
      <p class="service-line">Accounting, Tax &amp; Consulting Services</p>
    </div>
  </section>

  <section class="card card-back" aria-label="Card back">
    <div class="contact-block">
      <h1 class="person-name">Dario Whitcombe</h1>
      <p class="person-role">Principal</p>
      <ul class="contact-list">
        <li>
          <svg viewBox="0 0 24 24" aria-hidden="true"><path d="M6.6 10.8a15.1 15.1 0 0 0 6.6 6.6l2.2-2.2a1 1 0 0 1 1-.25 11.4 11.4 0 0 0 3.6.57 1 1 0 0 1 1 1V20a1 1 0 0 1-1 1A17 17 0 0 1 3 4a1 1 0 0 1 1-1h3.5a1 1 0 0 1 1 1c0 1.25.2 2.46.57 3.6a1 1 0 0 1-.25 1z"/></svg>
          044-555 210 377
        </li>
        <li>
          <svg viewBox="0 0 24 24" aria-hidden="true"><path d="M2 5h20v14H2zm2 2v.5l8 5 8-5V7zm0 2.8V17h16V9.8l-8 5z"/></svg>
          info@whitcombecpa.com
        </li>
      </ul>
      <p class="address">421, Address line goes here<br>45452,Country Name</p>
    </div>
  </section>
</main>
</body>
</html>
```